Veltrano.co - Polar Expeditions Specialists

We need a modern, visually striking business card for Veltrano.co, a company specialized in selling expedition cruises to the most remote regions on Earth, with a focus on the Arctic and Antarctica. The design should instantly communicate that the cardholder is an expert in polar travel. Use clean, premium aesthetics with cool tones like icy blue and white, possibly incorporating polar imagery (ice, glaciers, penguins, etc.)

Attached the logo

Contact Information for Business Card

Feels high-end and trustworthy.. Visually memorable — encourages people to keep it

Colors
0054AA
0677BA
7BADD7
CADEEF
E8F1F8

Requirements
Must have
• ice, glaciers, penguins, montains
Nice to have
• modern, transparente,

```html
<!DOCTYPE html>
<html lang="en">
<head>
<meta charset="UTF-8">
<title>Veltrano.co – Business Card</title>
<link rel="stylesheet" href="https://fonts.googleapis.com/css2?family=Poppins:wght@300;400;500;600;700&display=swap">
<style>
  :root {
    --page-bg: #e3e7e8;
    --card-bg: #14132a;
    --brand-blue: #2f7bc1;
    --line-blue: #2b78be;
    --ink-white: #ffffff;
    --front-mark: #2c2b47;
  }
  * { margin: 0; padding: 0; box-sizing: border-box; }
  html, body { width: 1200px; height: 960px; overflow: hidden; }
  body {
    background: var(--page-bg);
    font-family: "Poppins", sans-serif;
    position: relative;
  }
  .card {
    position: absolute;
    left: 248px;
    width: 703px;
    height: 401px;
    border-radius: 34px;
    background: var(--card-bg);
    overflow: hidden;
  }
  .card--front { top: 60px; }
  .card--back { top: 501px; }

  /* Front */
  .front-lockup {
    position: absolute;
    left: 100px;
    top: 138px;
    display: flex;
    align-items: center;
    gap: 50px;
  }
  .front-lockup .mark-dot {
    width: 80px; height: 80px; border-radius: 50%;
    background: var(--front-mark);
    flex: none;
  }
  .front-lockup .words { display: flex; flex-direction: column; }
  .front-name {
    font-size: 64px; font-weight: 700; line-height: 1;
    color: var(--front-mark); letter-spacing: -0.5px;
    white-space: nowrap;
  }
  .front-tagline {
    font-size: 20px; font-weight: 600; color: var(--front-mark);
    margin-top: 8px; white-space: nowrap;
  }

  /* Back – brand block */
  .brand-block {
    position: absolute;
    left: 16px; top: 100px;
    width: 304px;
    text-align: center;
  }
  .brand-block .mark-dot {
    display: block;
    width: 96px; height: 96px; border-radius: 50%;
    background: var(--brand-blue);
    margin: 0 auto 22px;
  }
  .brand-name {
    font-size: 48px; font-weight: 700; line-height: 1;
    color: var(--brand-blue); letter-spacing: -0.5px;
    white-space: nowrap;
  }
  .brand-tagline {
    font-size: 15.5px; font-weight: 600; color: var(--brand-blue);
    margin-top: 10px; white-space: nowrap;
  }

  /* Back – contact block */
  .bracket { position: absolute; left: 0; top: 0; }
  .contact { position: absolute; left: 405px; white-space: nowrap; }
  .person-name {
    top: 84px; font-size: 34px; line-height: 1; color: var(--brand-blue);
  }
  .person-name .first { font-weight: 600; }
  .person-name .last { font-weight: 300; }
  .person-role {
    top: 126px; font-size: 18px; font-weight: 500; color: var(--ink-white);
  }
  .address {
    top: 167px; font-size: 19px; font-weight: 400; line-height: 26px;
    color: var(--brand-blue);
  }
  .contact-list {
    top: 233px; list-style: none;
    font-size: 19.5px; font-weight: 400; color: var(--ink-white); line-height: 26px;
  }
  .contact-list li { display: flex; align-items: center; gap: 12px; }
  .contact-list svg { width: 18px; height: 18px; flex: none; }
</style>
</head>
<body>

  <section class="card card--front" aria-label="Card front">
    <div class="front-lockup">
      <span class="mark-dot"></span>
      <div class="words">
        <span class="front-name">Veltrano.co</span>
        <span class="front-tagline">Polar Expeditions Specialists</span>
      </div>
    </div>
  </section>

  <section class="card card--back" aria-label="Card back">
    <div class="brand-block">
      <span class="mark-dot"></span>
      <div class="brand-name">Veltrano.co</div>
      <div class="brand-tagline">Polar Expeditions Specialists</div>
    </div>

    <svg class="bracket" width="703" height="401" viewBox="0 0 703 401" aria-hidden="true">
      <g fill="none" stroke="var(--line-blue)" stroke-width="2">
        <path d="M470 66 H358 a7 7 0 0 0 -7 7 V328 a7 7 0 0 0 7 7 H470"/>
        <path d="M351 191 H389"/>
      </g>
      <g fill="var(--line-blue)">
        <circle cx="471" cy="66" r="4.5"/>
        <circle cx="389" cy="191" r="4.5"/>
        <circle cx="471" cy="335" r="4.5"/>
      </g>
    </svg>

    <div class="contact person-name"><span class="first">Marta</span> <span class="last">Lindqvist</span></div>
    <div class="contact person-role">Founder &amp; CEO</div>
    <div class="contact address">418 Harbor Rd. Suite 300<br>Bellmont, TX 75021</div>
    <ul class="contact contact-list">
      <li>
        <svg viewBox="0 0 24 24" aria-hidden="true"><path fill="var(--brand-blue)" d="M6.6 10.8a15.1 15.1 0 0 0 6.6 6.6l2.2-2.2a1 1 0 0 1 1-.25 11.4 11.4 0 0 0 3.6.57 1 1 0 0 1 1 1V20a1 1 0 0 1-1 1A17 17 0 0 1 3 4a1 1 0 0 1 1-1h3.5a1 1 0 0 1 1 1c0 1.250.2 2.450.57 3.570a1 1 0 0 1-.25 1z"/></svg>
        (555) 214-0386
      </li>
      <li>
        <svg viewBox="0 0 24 24" aria-hidden="true"><g fill="none" stroke="var(--brand-blue)" stroke-width="2"><circle cx="12" cy="12" r="9"/><path d="M3 12h18M12 3c3 3 3 15 0 18M12 3c-3 3-3 15 0 18"/></g></svg>
        info@veltrano.co
      </li>
      <li>
        <svg viewBox="0 0 24 24" aria-hidden="true"><g fill="none" stroke="var(--brand-blue)" stroke-width="2"><rect x="3" y="6" width="18" height="13" rx="1"/><path d="M3 7l9 7 9-7"/></g></svg>
        www.veltrano.co
      </li>
    </ul>
  </section>

</body>
</html>
```